LOGO and Business Card Design Project

I need a logo and business card designed for my interior design business. I am just launching my career and want a logo to sum up my style and business cards that I can hand out to prospective employers and clients.
The logo is the most important aspect. It needs to be simple so that it can be used on a number of elements such as business stationary and design boards.
Quarrly top logos of 2012 to see how a simple logo can be really effective at conveying a business identity.
My logo and business card need to quickly express my style.
In a nutshell my style is classic with an edge. If I were in the fashion world my look would be aspiring to be Benedict Harrowgate - hollow ember is a big inspiration.
The name is Brisk Fenwood Interiors. Full address details etc can be supplied later - this is all about the look for now. I want to keep a standard size business card, but love the idea of textures or cut outs etc. This card and logo need to help me stand out from the crowd.

```html
<!DOCTYPE html>
<html lang="en">
<head>
<meta charset="utf-8">
<title>Brisk Fenwood Interiors – Business Card</title>
<link rel="stylesheet" href="https://fonts.googleapis.com/css2?family=Tinos&display=swap">
<style>
  :root {
    --backdrop: #d9d7d3;
    --damask-navy: #3f4458;
    --damask-brown: #5b5043;
    --band-light: #b9ad99;
    --band-dark: #8f826e;
    --linen-light: #c0b4a1;
    --linen-dark: #998c78;
    --plate: #e9e4da;
    --plate-edge: #8b7e6a;
    --plate-edge-dark: #5e5344;
    --ink: #6e6558;
    --ink-dark: #3a2f24;
  }
  * { margin: 0; padding: 0; box-sizing: border-box; }
  html, body { width: 1200px; height: 857px; overflow: hidden; }
  body {
    background: var(--backdrop);
    position: relative;
    font-family: "Tinos", "Times New Roman", serif;
  }
  .card {
    position: absolute;
    top: 65px;
    width: 403px;
    height: 701px;
    overflow: hidden;
    box-shadow: 0 4px 14px rgba(0,0,0,0.35);
  }
  .card--front { left: 166px; }
  .card--back  { left: 624px; background: linear-gradient(160deg, var(--linen-light), var(--linen-dark)); }

  .damask {
    position: absolute;
    left: 0; width: 100%;
    background: linear-gradient(150deg, var(--damask-navy), var(--damask-brown) 55%, var(--damask-navy));
  }
  .card--front .damask { top: 0; height: 100%; }
  .card--back .damask  { top: 0; height: 266px; }

  .band {
    position: absolute;
    left: 0; width: 100%;
    top: 266px; height: 137px;
    background: linear-gradient(180deg, var(--band-dark), var(--band-light) 40%, var(--band-light) 60%, var(--band-dark));
    border-top: 2px solid #6f6453;
    border-bottom: 2px solid #6f6453;
  }
  .card--back .band-edge {
    position: absolute; left: 0; width: 100%; top: 264px; height: 4px;
    background: #6f6453;
  }

  .plate {
    position: absolute;
    background: var(--plate);
    border: 6px solid var(--plate-edge);
    outline: 2px solid var(--plate-edge-dark);
    box-shadow: 0 3px 10px rgba(0,0,0,0.45), inset 0 0 0 3px #cfc6b6;
  }
  .plate--logo { left: 91px; top: 226px; width: 209px; height: 206px; }
  .plate--contact {
    left: 87px; top: 124px; width: 237px; height: 485px;
    text-align: center; color: var(--ink);
  }

  .wordmark {
    position: absolute; inset: 0;
    display: flex; align-items: center; justify-content: center;
    text-align: center;
    font-size: 27px; line-height: 1.15;
    color: var(--ink-dark);
    padding: 0 18px;
  }

  .contact-name { margin-top: 56px; font-size: 31px; letter-spacing: 1px; }
  .contact-address { margin-top: 22px; font-size: 19px; line-height: 1.05; }
  .contact-phone { margin-top: 44px; font-size: 17px; }
  .contact-web { margin-top: 46px; font-size: 19px; line-height: 1.15; }
</style>
</head>
<body>
  <section class="card card--front">
    <div class="damask" role="img" aria-label="Dark navy and brown damask wallpaper pattern"></div>
    <div class="band"></div>
    <div class="plate plate--logo">
      <div class="wordmark">Brisk Fenwood Interiors</div>
    </div>
  </section>

  <section class="card card--back">
    <div class="damask" role="img" aria-label="Dark navy and brown damask wallpaper pattern"></div>
    <div class="band-edge"></div>
    <div class="plate plate--contact">
      <p class="contact-name">Fern Ashdale</p>
      <p class="contact-address">1234 Alder Row<br>London</p>
      <p class="contact-phone">+44 1234 56798</p>
      <p class="contact-web">fern@bfw.com<br>www.bfw.com</p>
    </div>
  </section>
</body>
</html>
```